Web Design for a Biotech Consulting Firm

We need a web site design for a new business based in Philadelphia called Verantel Dx. This is a consulting firm that will serve medical diagnostics industry, which is part of the life science/healthcare industry focusing on developing and marketing products that help in early detection, monitoring or management of diseases. Our consulting firm will help medical diagnostic companies to overcome key challenges in designing, evaluating and marketing new products.Our company name is Verantel Dx. Verantel is Latin word for "something" Dx represents diagnostics. The idea behind the name is that we help companies to transform the original, early product ideas ("nothing") into "something"; which is a product with full clinical utility that will help to improve health and well-being.The web site should use the visual feel of the logo (attached), be modern, simple and clean looking and represent creativity, innovation, scientific thinking and progress.
Updates

Wix Design is acceptable

Industry/Entity Type

Biotechnology

Coding

Coded - Design and coding required

Number of Pages Required

1 page

Font styles to use
Sans Serif

Requirements
Must have
• simple, clean look couple of pages
Should not have
• a lot of pages

```html
<!DOCTYPE html>
<html lang="en">
<head>
<meta charset="utf-8">
<title>Verantel Dx — Biotech Consulting</title>
<link rel="stylesheet" href="https://fonts.googleapis.com/css2?family=Montserrat:wght@400;500;600;700&family=Poppins:wght@300;400;500;600&display=swap">
<style>
:root{
  --blue:#2a6fe0;
  --blue-dark:#1e4fa8;
  --navy:#1c2a5a;
  --ink:#222;
  --text:#555;
  --muted:#777;
  --footer:#f0f1f3;
  --dark-box:rgba(20,20,22,.88);
  --white:#fff;
}
*{box-sizing:border-box;margin:0;padding:0}
html,body{width:1200px;height:5000px;overflow:hidden}
body{position:relative;background:var(--white);font-family:"Poppins",sans-serif;color:var(--text)}
.abs{position:absolute}
h1,h2,h3{font-family:"Montserrat",sans-serif;font-weight:500;color:var(--ink)}
.btn{position:absolute;display:flex;align-items:center;justify-content:center;font-family:"Montserrat",sans-serif;font-weight:600;font-size:14px;letter-spacing:.3px;text-transform:uppercase}
.btn-blue{background:var(--blue);color:var(--white)}
.btn-dark{background:#1a1a1a;color:var(--white)}
.rule{position:absolute;height:4px;width:70px;background:var(--blue)}

/* hero */
.hero-photo{left:0;top:0;width:1200px;height:777px;background:linear-gradient(120deg,#d9e1ea 0%,#9fb0c2 45%,#5a6c82 75%,#c9d3de 100%)}
.brand{font-family:"Montserrat",sans-serif;font-weight:500;color:var(--navy)}
.logo-top{left:142px;top:70px;font-size:28px}
.call{left:680px;top:38px;display:flex;align-items:center;gap:14px}
.call-icon{width:38px;height:38px;border-radius:50%;background:var(--blue);display:flex;align-items:center;justify-content:center}
.call small{display:block;font-size:12px;color:var(--ink);font-weight:500}
.call strong{font-family:"Montserrat",sans-serif;font-size:21px;color:var(--ink);font-weight:600}
.nav{left:462px;top:108px;display:flex;gap:40px;font-family:"Montserrat",sans-serif;font-weight:600;font-size:15px;color:var(--ink)}
.promo{background:var(--dark-box);color:var(--white);width:410px;height:243px;padding:30px 40px;white-space:nowrap}
.promo h1,.promo h2{color:var(--white)}
.promo h1{font-size:48px;line-height:58px;font-weight:500}
.promo h2{font-size:31px;line-height:40px;font-weight:400}
.promo .btn{left:46px;top:160px;height:40px;width:168px;font-size:13px}
.dots{left:128px;top:606px;display:flex;gap:12px}
.dots span{width:14px;height:14px;border-radius:50%;background:var(--white)}
.dots span:first-child{box-shadow:0 0 0 3px rgba(255,255,255,.5);border:2px solid #333}

/* about */
.about-title{position:absolute;left:142px;top:864px;font-size:38px}
.about-title span{color:var(--blue)}
.about-text{position:absolute;left:142px;top:966px;width:450px;font-size:15px;line-height:33.5px;color:var(--text)}
.btn-outline{left:142px;top:1192px;width:153px;height:41px;border:3px solid var(--blue);color:var(--blue)}
.about-frame{left:658px;top:874px;width:398px;height:359px;border:5px solid var(--blue-dark)}
.about-photo{left:670px;top:887px;width:375px;height:333px;background:radial-gradient(circle at 55% 50%,#c9a64a 0%,#5a6f8e 30%,#1b2d5a 70%,#0f1a3a 100%)}

/* features */
.features{left:0;top:1350px;width:1200px;height:936px;background:linear-gradient(180deg,#e4e8ee,#eef1f5)}
.sec-title{position:absolute;left:0;width:1200px;text-align:center;font-size:46px}
.lead{position:absolute;left:210px;top:1538px;width:780px;text-align:center;font-size:14.5px;line-height:28px;color:#444}
.card{position:absolute;width:296px;height:245px;background:var(--white);border:1px solid #dde1e7;text-align:center;padding-top:22px}
.card.active{border:5px solid var(--blue);padding-top:18px}
.card svg{width:72px;height:72px}
.card h3{font-size:18px;font-weight:500;margin-top:10px;color:#333}
.card p{font-size:12px;line-height:23px;color:var(--muted);margin:8px 14px 0}

/* banner */
.banner-photo{left:0;top:2286px;width:1200px;height:526px;background:linear-gradient(100deg,#5c7fa6 0%,#8fb1d1 35%,#c4d4e2 60%,#e2e7ec 100%)}

/* consulting */
.cons{position:absolute;width:293px;height:335px;border:5px solid var(--blue);border-top:none}
.cons.mid{border-top:5px solid var(--blue);border-bottom:none}
.cons .photo{position:absolute;left:-5px;width:293px}
.cons p{position:absolute;left:8px;right:8px;text-align:center;font-size:12.5px;line-height:25px;color:#444}
.cons .label{position:absolute;left:0;right:0;text-align:center;line-height:26px}
.cons .label span{background:var(--white);padding:0 12px;font-size:18px;color:var(--blue);font-family:"Montserrat",sans-serif}

/* quote */
.quote{left:0;top:3492px;width:1200px;height:592px;background:linear-gradient(90deg,#2d6fe0,#2a66d8 50%,#2f73e6)}
.q-frame{left:352px;top:3552px;width:497px;height:470px;border:7px solid var(--white)}
.q-gap{left:840px;top:3760px;width:20px;height:110px;background:#2c6ce0}
.q-title{position:absolute;left:390px;top:3588px;font-size:35px;color:var(--white);font-weight:500}
.field{position:absolute;left:390px;width:416px;height:34px;background:var(--white);font-size:11px;color:#666;padding:9px 16px}
.field.msg{height:74px}

/* testimonial */
.avatar{left:186px;top:4184px;width:176px;height:176px;border-radius:50%;border:4px solid var(--blue);background:radial-gradient(circle at 50% 40%,#b8c2cf,#55667d)}
.qmark{left:372px;top:4160px;font-family:Georgia,serif;font-size:110px;line-height:1;color:#c9ccd2}
.t-title{left:429px;top:4186px;font-family:"Montserrat",sans-serif;font-weight:600;font-size:18px;line-height:32px;color:var(--ink)}
.t-meta{left:429px;top:4250px;display:flex;gap:14px;align-items:center;font-size:15px;color:#333}
.t-text{left:429px;top:4292px;width:590px;font-size:12.5px;line-height:26px;color:#444}

/* footer */
.footer{left:0;top:4476px;width:1200px;height:350px;background:var(--footer)}
.logo-foot{left:152px;top:4588px;font-size:28px}
.f-about{left:134px;top:4680px;width:350px;font-size:12.5px;line-height:26px;color:#555}
.f-head{font-family:"Montserrat",sans-serif;font-weight:500;font-size:17px;color:var(--ink);letter-spacing:.3px}
.f-item{left:524px;display:flex;gap:16px;font-size:13px;line-height:21px;color:#333}
.f-item svg{flex:none;margin-top:3px}
.news-text{left:792px;top:4590px;width:280px;font-size:12.5px;line-height:24px;color:#555}
.news-input{left:792px;top:4647px;width:276px;height:39px;background:var(--white);border:1px solid #d6d9de;font-size:11px;padding:11px 12px;color:#666}
.social{left:540px;top:4876px;display:flex;gap:16px}
.social span{width:32px;height:32px;border-radius:50%;border:2px solid #333}
.copy{left:0;top:4936px;width:1200px;text-align:center;font-size:13.5px;color:#333}
</style>
</head>
<body>

<!-- hero -->
<div class="abs hero-photo" role="img" aria-label="Scientist in a lab coat and blue gloves working at a microscope in a bright laboratory"></div>
<div class="abs brand logo-top">Verantel Dx</div>
<div class="abs call">
  <div class="call-icon"><svg width="18" height="18" viewBox="0 0 24 24"><path fill="#fff" d="M6.6 10.8a15.1 15.1 0 0 0 6.6 6.6l2.2-2.2c.3-.3.7-.4 1-.2 1.1.4 2.3.6 3.6.6.6 0 1 .4 1 1V20c0 .6-.4 1-1 1A17 17 0 0 1 3 4c0-.6.4-1 1-1h3.5c.6 0 1 .4 1 1 0 1.3.2 2.5.6 3.6.1.3 0 .7-.2 1z"/></svg></div>
  <div><small>CALL US :</small><strong>215-640-0193</strong></div>
</div>
<div class="btn btn-blue" style="left:916px;top:39px;width:140px;height:39px">Get a quote</div>
<nav class="abs nav"><span>HOME</span><span>ABOUT US</span><span>OUR SERVICES</span><span>PRODUCTS</span><span>CONTACT US</span></nav>
<div class="abs promo" style="left:124px;top:330px">
  <h1>Verantel Dx</h1>
  <h2>Biotech consulting</h2>
  <div class="btn btn-blue">Get more info</div>
</div>
<div class="abs dots"><span></span><span></span><span></span><span></span></div>

<!-- about -->
<section class="about">
  <h2 class="about-title">About <span>Verantel Dx</span></h2>
  <div class="rule" style="left:142px;top:932px"></div>
  <p class="about-text">Sed ut perspiciatis unde omnis iste natus error sit voluptatem accusantium doloremque laudantium, totam rem aperiam, eaque ipsa quae ab illo inventore veritatis et quasi architecto beatae vitae dicta sunt explicabo. Nemo enim ipsam vptatem quia voluptas sit aspernatur aut odit aut fugit, sed quia consequuntur magni dolores eos</p>
  <div class="btn btn-outline">Read more</div>
  <div class="abs about-frame"></div>
  <div class="abs about-photo" role="img" aria-label="Researcher studying a glowing holographic brain model above a tablet"></div>
</section>

<!-- features -->
<div class="abs features"></div>
<h2 class="sec-title" style="top:1422px">Verantel Dx Features</h2>
<div class="rule" style="left:565px;top:1497px"></div>
<p class="lead">Sed ut perspiciatis unde omnis iste natus error sit voluptatem accusantium doloremque laudantium, totam rem aperiam, eaque ipsa quae ab illo inventore veritatis et quasi architecto beatae vitae dicta</p>

<div class="card" style="left:132px;top:1656px">
  <svg viewBox="0 0 80 80" fill="none" stroke="#2a6fe0" stroke-width="2.5"><path d="M30 10h14M34 10v20L20 60c-2 5 1 10 6 10h22c5 0 8-5 6-10L40 30V10"/><path d="M24 52h26"/><circle cx="58" cy="22" r="6"/><circle cx="62" cy="40" r="4"/></svg>
  <h3>Quis autem vel eum</h3>
  <p>Sed ut perspiciatis unde omnis iste natus error sit voluptatem accusantium doreque laudantium, totam rem aperiam</p>
</div>
<div class="card active" style="left:452px;top:1656px">
  <svg viewBox="0 0 80 80" fill="none" stroke="#2a6fe0" stroke-width="2.5"><path d="M40 72V36"/><path d="M40 44C22 44 12 32 12 14c18 0 28 12 28 30z"/><path d="M40 40c0-16 10-26 28-26 0 16-10 26-28 26z"/></svg>
  <h3>Quis autem vel eum</h3>
  <p>Sed ut perspiciatis unde omnis iste natus error sit voluptatem accusantium doreque laudantium, totam rem aperiam</p>
</div>
<div class="card" style="left:773px;top:1656px">
  <svg viewBox="0 0 80 80" fill="none" stroke="#2a6fe0" stroke-width="2.5"><rect x="10" y="12" width="50" height="40" rx="2"/><path d="M10 20h50"/><circle cx="48" cy="46" r="14"/><path d="M58 56l12 12"/><path d="M42 50v-6M47 50v-9M52 50v-4"/></svg>
  <h3>Quis autem vel eum</h3>
  <p>Sed ut perspiciatis unde omnis iste natus error sit voluptatem accusantium doreque laudantium, totam rem aperiam</p>
</div>
<div class="card" style="left:132px;top:1928px">
  <svg viewBox="0 0 80 80" fill="none" stroke="#2a6fe0" stroke-width="2.5"><rect x="8" y="8" width="64" height="64" rx="3"/><path d="M8 20h64"/><rect x="28" y="40" width="24" height="20" rx="2"/><path d="M32 40v-6a8 8 0 0 1 16 0v6"/><circle cx="40" cy="50" r="3"/></svg>
  <h3>Quis autem vel eum</h3>
  <p>Sed ut perspiciatis unde omnis iste natus error sit voluptatem accusantium doreque laudantium, totam rem aperiam</p>
</div>
<div class="card" style="left:452px;top:1928px">
  <svg viewBox="0 0 80 80" fill="none" stroke="#2a6fe0" stroke-width="2.5"><circle cx="40" cy="14" r="6"/><circle cx="16" cy="52" r="6"/><circle cx="64" cy="52" r="6"/><path d="M30 18L20 40M50 18l10 22M26 62h28"/><path d="M6 74c0-8 20-8 20 0M54 74c0-8 20-8 20 0"/></svg>
  <h3>Quis autem vel eum</h3>
  <p>Sed ut perspiciatis unde omnis iste natus error sit voluptatem accusantium doreque laudantium, totam rem aperiam</p>
</div>
<div class="card" style="left:773px;top:1928px">
  <svg viewBox="0 0 80 80" fill="none" stroke="#2a6fe0" stroke-width="2.5"><path d="M40 74V30M40 50L22 36M40 44l18-12M40 36L28 20M40 36l12-16"/><circle cx="40" cy="26" r="4"/><circle cx="20" cy="34" r="4"/><circle cx="60" cy="30" r="4"/><circle cx="26" cy="16" r="4"/><circle cx="54" cy="16" r="4"/><path d="M28 74h24"/></svg>
  <h3>Quis autem vel eum</h3>
  <p>Sed ut perspiciatis unde omnis iste natus error sit voluptatem accusantium doreque laudantium, totam rem aperiam</p>
</div>

<!-- banner -->
<div class="abs banner-photo" role="img" aria-label="Laboratory technician in safety glasses and blue gloves handling sample trays"></div>
<div class="abs promo" style="left:124px;top:2414px">
  <h1>Medical</h1>
  <h2>Diagnostics Industry</h2>
  <div class="btn btn-blue">Get more info</div>
</div>

<!-- consulting -->
<h2 class="sec-title" style="top:2880px;font-size:40px">Our Consulting</h2>
<div class="rule" style="left:568px;top:2952px"></div>

<div class="cons" style="left:134px;top:3031px">
  <div class="photo" role="img" aria-label="Scientist pipetting samples in a life science lab" style="top:0;height:211px;background:linear-gradient(135deg,#cfd9e4,#8ea3bb)"></div>
  <p style="top:222px">Sed ut perspiciatis unde omnis iste natus error sit voluptatem accusantium doque laium, totam rem aperiam</p>
  <div class="label" style="bottom:-15px"><span>Life Science</span></div>
</div>
<div class="cons mid" style="left:454px;top:3031px">
  <div class="label" style="top:-16px"><span>Healthcare</span></div>
  <p style="top:28px">Sed ut perspiciatis unde omnis iste natus error sit voluptatem accusantium doque laium, totam rem aperiam</p>
  <div class="photo" role="img" aria-label="Hospital operating room with imaging equipment" style="top:124px;height:211px;background:linear-gradient(135deg,#9aa9bc,#3f5069)"></div>
</div>
<div class="cons" style="left:775px;top:3031px">
  <div class="photo" role="img" aria-label="Doctor preparing a patient for a scanner exam" style="top:0;height:211px;background:linear-gradient(135deg,#e3e7ec,#9aa8b8)"></div>
  <p style="top:222px">Sed ut perspiciatis unde omnis iste natus error sit voluptatem accusantium doque laium, totam rem aperiam</p>
  <div class="label" style="bottom:-15px"><span>Diagnostics</span></div>
</div>

<!-- quote form -->
<div class="abs quote" role="img" aria-label="Blue-tinted laboratory background"></div>
<div class="abs q-frame"></div>
<div class="abs q-gap"></div>
<h2 class="q-title">Request A Free Quote</h2>
<div class="field" style="top:3653px">First Name</div>
<div class="field" style="top:3702px">Company Name</div>
<div class="field" style="top:3750px">Email Address</div>
<div class="field" style="top:3799px">Phone Number</div>
<div class="field msg" style="top:3849px">Message :</div>
<div class="btn btn-dark" style="left:390px;top:3942px;width:224px;height:41px">Submit now</div>

<!-- testimonial -->
<svg class="abs" style="left:122px;top:4266px" width="24" height="36" viewBox="0 0 24 36"><path d="M20 2L4 18l16 16" fill="none" stroke="#777" stroke-width="3"/></svg>
<svg class="abs" style="left:1054px;top:4266px" width="24" height="36" viewBox="0 0 24 36"><path d="M4 2l16 16L4 34" fill="none" stroke="#777" stroke-width="3"/></svg>
<div class="abs avatar" role="img" aria-label="Portrait photo of a client"></div>
<div class="abs qmark">&ldquo;</div>
<div class="abs t-title">QUIS AUTEM VEL EUM IURE REPREHENDERIT<br>QUI IN EA VOLUPTATE VELIT ESSE</div>
<div class="abs t-meta">
  <svg width="106" height="18" viewBox="0 0 106 18" fill="none" stroke="#2a6fe0" stroke-width="1.5"><g id="s"><path d="M9 1l2.4 5.2 5.6.6-4.2 3.8 1.2 5.6L9 13.3 4 16.2l1.2-5.6L1 6.8l5.6-.6z"/></g><use href="#s" x="22"/><use href="#s" x="44"/><use href="#s" x="66"/><use href="#s" x="88"/></svg>
  <span>January 3, 2019</span>
</div>
<p class="abs t-text">Sed ut perspiciatis unde omnis iste natus error sit voluptatem accusantium doloremque laudantium, totam rem aperiam, eaque ipsa quae ab illo inventore veritatis et quasi architecto beatae vitae dicta sunt explicabo. Nemo enim ipsam voluptatem quia voluptas sit aspernatur aut odit aut fugit, sed quia consequuntur magni dolores</p>

<!-- footer -->
<footer>
  <div class="abs footer"></div>
  <div class="abs brand logo-foot">Verantel Dx</div>
  <p class="abs f-about">Sed ut perspiciatis unde omnis iste natus error sit voluptatem accusantium doloque laudantium, totam rem aperiam, eaque ipsa quae ab illo inventore</p>
  <div class="abs f-head" style="left:524px;top:4546px">CONTACT US</div>
  <div class="abs f-item" style="top:4598px"><svg width="12" height="16" viewBox="0 0 12 16"><path fill="#2a6fe0" d="M6 0a6 6 0 0 0-6 6c0 4.5 6 10 6 10s6-5.5 6-10a6 6 0 0 0-6-6zm0 8.5A2.5 2.5 0 1 1 6 3.5a2.5 2.5 0 0 1 0 5z"/></svg><div>Verantel Dx<br>Philadelphia, PA, 19103</div></div>
  <div class="abs f-item" style="top:4648px"><svg width="12" height="14" viewBox="0 0 24 24"><path fill="#2a6fe0" d="M6.6 10.8a15.1 15.1 0 0 0 6.6 6.6l2.2-2.2c.3-.3.7-.4 1-.2 1.1.4 2.3.6 3.6.6.6 0 1 .4 1 1V20c0 .6-.4 1-1 1A17 17 0 0 1 3 4c0-.6.4-1 1-1h3.5c.6 0 1 .4 1 1 0 1.3.2 2.5.6 3.6.1.3 0 .7-.2 1z"/></svg><div>Phone:<br>(215) 640 - 0193</div></div>
  <div class="abs f-item" style="top:4700px"><svg width="12" height="12" viewBox="0 0 12 10"><path fill="#2a6fe0" d="M0 0h12v10H0z"/><path d="M0 0l6 5 6-5" fill="none" stroke="#fff"/></svg><div>Email:<br>info@veranteldx.com</div></div>
  <div class="abs f-head" style="left:792px;top:4544px">SIGN UP FOR NEWSLETTER</div>
  <p class="abs news-text">Quis autem vel eum iure reprehenderit qui in ea voluptate velit esse quam nihil</p>
  <div class="abs news-input">Enter email</div>
  <div class="btn btn-blue" style="left:792px;top:4701px;width:113px;height:35px;font-size:12px">Subscribe</div>
  <div class="abs social" aria-label="Social links"><span></span><span></span><span></span></div>
  <p class="abs copy">Verantel Dx © 2019 All Rights Reserved | Privacy Policy | Terms and Conditions</p>
</footer>

</body>
</html>
```